Brell Stone Company Business Cards

Front and Back Business Card - logo and text setup - cool design. I need workable photoshop or illustrator files so I can setup each employee card with design that is created
Updates

Hi everyone, thank you for the great entries. Please no more white and blue cards - there are so many already - black and silver only now please. thanks!

Target Market(s)

Construction Industry - Facility Managers

Industry/Entity Type

Construction

Contact Information for Business Card

I really like contemporary simplistic looks - clean neat....not opposed to seeing some black backrounds

Requirements
Must have
• Logo/website address with design on front only - www.brellstone-example.com (logo attached)
• Back:
• Name/Title/Company Address/Phone/email address
Nice to have
• Cool design
Should not have
• Nothing gimmicky like Fire or Water - since we are a Fire Protection company - it has all been done

```html
<!DOCTYPE html>
<html lang="en">
<head>
<meta charset="utf-8">
<title>Brell Stone Company Business Cards</title>
<link rel="stylesheet" href="https://fonts.googleapis.com/css2?family=Open+Sans:ital,wght@0,400;0,700;1,700&display=swap">
<style>
  :root {
    --page-bg: #1c1c1e;
    --card-black: #050505;
    --silver: #8a8a8a;
    --silver-light: #c8c8c8;
    --brand-blue: #0a22a0;
    --brand-red: #f2242a;
    --white: #ffffff;
  }
  * { margin: 0; padding: 0; box-sizing: border-box; }
  html, body {
    width: 1200px; height: 960px; overflow: hidden;
    background: var(--page-bg);
    font-family: "Open Sans", Arial, sans-serif;
  }
  .card-sheet {
    width: 1200px; height: 960px;
    display: flex; flex-direction: column; align-items: center; justify-content: center;
    gap: 32px;
  }
  .card {
    position: relative;
    width: 760px; height: 434px;
    background: var(--card-black);
    overflow: hidden;
  }
  /* Front */
  .card-front {
    display: flex; flex-direction: column; align-items: center; justify-content: center;
  }
  .wordmark {
    font-weight: 700;
    letter-spacing: -1px;
    line-height: 1;
  }
  .card-front .wordmark { font-size: 92px; color: var(--silver); }
  .card-front .website {
    margin-top: 40px;
    font-size: 17px; letter-spacing: 4px;
    color: var(--silver-light);
  }
  /* Back */
  .card-back .wordmark {
    position: absolute; left: 70px; top: 120px;
    font-size: 54px; color: var(--brand-blue);
  }
  .contact-disc {
    position: absolute; left: 0; top: 0;
    width: 760px; height: 434px;
  }
  .contact-block {
    position: absolute; right: 56px; top: 132px;
    text-align: right; color: var(--white);
  }
  .person-name, .person-title {
    font-weight: 700; font-style: italic; font-size: 22px; line-height: 1.2;
  }
  .address { margin-top: 12px; font-size: 18px; line-height: 1.3; }
  .contact-lines { margin-top: 14px; list-style: none; font-size: 18px; line-height: 1.55; }
  .contact-lines li { display: flex; align-items: center; justify-content: flex-end; gap: 10px; }
  .contact-lines svg { width: 16px; height: 16px; flex: none; }
</style>
</head>
<body>
<main class="card-sheet">
  <section class="card card-front" aria-label="Card front">
    <div class="wordmark">Brell Stone</div>
    <div class="website">www.brellstone-example.com</div>
  </section>

  <section class="card card-back" aria-label="Card back">
    <div class="wordmark">Brell Stone</div>
    <svg class="contact-disc" viewBox="0 0 760 434" aria-hidden="true">
      <circle cx="632" cy="320" r="268" fill="var(--brand-red)"/>
      <circle cx="648" cy="326" r="262" fill="var(--brand-blue)"/>
    </svg>
    <div class="contact-block">
      <p class="person-name">Dana Whitlow</p>
      <p class="person-title">President</p>
      <p class="address">48 Harbor Works Road<br>Millbrook, NY 10000</p>
      <ul class="contact-lines">
        <li>(555) 014-2290
          <svg viewBox="0 0 16 16" aria-hidden="true"><path d="M4 1.5l2.5 3-1.5 1.6a8 8 0 0 0 4.9 4.9l1.6-1.5 3 2.5-1.6 2.5C7.5 14.5 1.5 8.5 1.5 3.1z" fill="var(--white)"/></svg>
        </li>
        <li>info@brellstone-example.com
          <svg viewBox="0 0 16 16" aria-hidden="true"><rect x="1" y="3" width="14" height="10" fill="none" stroke="var(--white)" stroke-width="1.5"/><path d="M1 3l7 6 7-6" fill="none" stroke="var(--white)" stroke-width="1.5"/></svg>
        </li>
        <li>www.brellstone-example.com
          <svg viewBox="0 0 16 16" aria-hidden="true"><g fill="none" stroke="var(--white)" stroke-width="1.3"><circle cx="8" cy="8" r="6.5"/><ellipse cx="8" cy="8" rx="3" ry="6.5"/><path d="M1.5 8h13M2.5 4.8h11M2.5 11.2h11"/></g></svg>
        </li>
      </ul>
    </div>
  </section>
</main>
</body>
</html>
```